Sales sheet for printing and embroidery apparel items - Copper Hollow Graphics

I would like a one page flyer or sales sheet that I would use as a template to send different images of apparel we produce. I have attached examples of layouts I like.
- Ideally, it would have space for 3-5 items.
- I would like it one page only - not a folding flyer.
- Our companies name is Copper Hollow Graphics.
- This will be used for many different products and markets so I don't need wording/copy. You can use wording from the 7M9 or T58 flyer.

Colors
0054AA
0677BA
7BADD7
CADEEF
E8F1F8
00AB8E
00BBA5
67D7C9
C6EFE9
E9F9F6
FFC000
F8CF3A
FAE287
FDF2CF
FEFAEE

Requirements
Must have
• Places for between 3 and 5 images of apparel (t-shirts, hats etc)

```html
<!DOCTYPE html>
<html lang="en">
<head>
<meta charset="UTF-8">
<title>Copper Hollow Graphics – Apparel Sales Sheet</title>
<link rel="stylesheet" href="https://fonts.googleapis.com/css2?family=Montserrat:wght@400;500;600;700;800;900&family=Roboto:wght@700&display=swap">
<style>
  :root {
    --navy: #1b3a6b;
    --orange: #e46c3f;
    --paper: #f5f6f8;
    --backdrop: #bdbec0;
    --ink: #1d2433;
    --white: #ffffff;
  }
  * { box-sizing: border-box; margin: 0; padding: 0; }
  html, body { width: 1200px; height: 1200px; overflow: hidden; }
  body {
    background: var(--backdrop);
    font-family: "Montserrat", sans-serif;
    color: var(--navy);
    position: relative;
  }
  .sheet {
    position: absolute;
    left: 190px; top: 20px;
    width: 820px; height: 1160px;
    background: var(--paper);
    overflow: hidden;
  }
  .abs { position: absolute; }

  /* masthead */
  .masthead-band { left: 0; top: 152px; width: 820px; height: 76px; background: var(--orange); }
  .brand-name {
    left: 40px; top: 118px; width: 640px;
    text-align: center;
    font-weight: 900; font-size: 58px; line-height: 1.2;
    color: var(--navy);
  }
  .brand-square { left: 710px; top: 199px; width: 73px; height: 66px; background: var(--navy); }
  .est { left: 700px; top: 264px; width: 93px; text-align: center; font-weight: 700; font-size: 14px; color: var(--navy); }

  /* title */
  .sheet-title {
    left: 0; top: 410px; width: 820px; text-align: center;
    font-family: "Roboto", sans-serif; font-weight: 700; font-size: 46px;
    color: var(--orange); letter-spacing: 0.5px;
  }
  .rule { left: 72px; width: 676px; height: 1.5px; background: var(--ink); }
  .rule-top { top: 475px; }
  .rule-bottom { top: 510px; }
  .meta {
    left: 72px; top: 481px; width: 676px; text-align: center;
    font-size: 18.5px; color: var(--ink); white-space: nowrap;
  }
  .meta b { color: var(--navy); font-weight: 700; }
  .meta .gap { display: inline-block; width: 16px; }

  /* products */
  .product { top: 533px; width: 170px; }
  .product-shot { width: 170px; height: 217px; display: block; }
  .product-label {
    margin-top: 16px; text-align: center;
    font-size: 13px; font-weight: 500; line-height: 1.2; color: var(--navy);
  }

  /* warning */
  .warning-icon { left: 120px; top: 822px; width: 48px; height: 42px; }
  .warning-text {
    left: 170px; top: 824px; width: 600px; text-align: center;
    font-size: 16px; line-height: 1.25; color: var(--navy);
  }
  .warning-text b { font-weight: 700; }

  /* services band */
  .services { left: 0; top: 912px; width: 820px; height: 102px; background: var(--navy); }
  .service-icon { top: 22px; width: 58px; height: 58px; }
  .service-copy { top: 24px; color: var(--white); font-size: 13.5px; line-height: 1.18; }
  .service-copy h3 { font-size: 13px; font-weight: 700; letter-spacing: 0.3px; }
  .divider { top: 17px; width: 1.5px; height: 62px; background: var(--orange); }

  /* footer */
  .footer-square { left: 54px; top: 1033px; width: 64px; height: 56px; background: var(--navy); }
  .footer-name {
    left: 40px; top: 1094px; width: 92px; text-align: center;
    font-weight: 800; font-size: 11px; line-height: 1.1; color: var(--navy);
  }
  .about { left: 146px; top: 1038px; width: 272px; font-size: 12.3px; line-height: 1.22; color: var(--navy); }
  .about h3 { font-size: 14px; font-weight: 700; }
  .contact { right: 44px; top: 1040px; text-align: right; color: var(--navy); }
  .contact h3 { font-size: 13px; font-weight: 700; }
  .contact .phone { font-size: 34px; font-weight: 600; color: var(--orange); line-height: 1.2; margin-top: 2px; }
  .contact .web { font-size: 12.5px; margin-top: 1px; }
</style>
</head>
<body>
<main class="sheet">
  <div class="abs masthead-band"></div>
  <h1 class="abs brand-name">COPPER HOLLOW<br>GRAPHICS</h1>
  <div class="abs brand-square"></div>
  <div class="abs est">Est. 1979</div>

  <h2 class="abs sheet-title">APPAREL SALES SHEET</h2>
  <div class="abs rule rule-top"></div>
  <p class="abs meta"><b>Category:</b> Printing &amp; Embroidery Apparel<span class="gap"></span><b>Use:</b> Flexible Sales Template</p>
  <div class="abs rule rule-bottom"></div>

  <section class="abs product" style="left:51px">
    <svg class="product-shot" viewBox="0 0 170 217" role="img" aria-label="Black hoodie with embroidered red and white front graphic">
      <rect x="8" y="10" width="154" height="200" rx="22" fill="#161616"/>
    </svg>
    <p class="product-label">PREMIUM<br>EMBROIDERY</p>
  </section>
  <section class="abs product" style="left:234px">
    <svg class="product-shot" viewBox="0 0 170 217" role="img" aria-label="Black trucker cap with gold embroidered front lettering">
      <path d="M10 180 Q10 40 85 38 Q160 40 160 180 Z" fill="#1a1a1a"/>
    </svg>
    <p class="product-label">CUSTOM<br>HEADWEAR</p>
  </section>
  <section class="abs product" style="left:416px">
    <svg class="product-shot" viewBox="0 0 170 217" role="img" aria-label="Navy t-shirt with screen printed space illustration">
      <defs><linearGradient id="tee" x1="0" y1="0" x2="0" y2="1"><stop offset="0" stop-color="#1a2560"/><stop offset="1" stop-color="#121b4a"/></linearGradient></defs>
      <path d="M55 4 L115 4 L168 40 L150 78 L132 68 L132 210 L38 210 L38 68 L20 78 L2 40 Z" fill="url(#tee)"/>
    </svg>
    <p class="product-label">SCREEN PRINTED<br>TEES</p>
  </section>
  <section class="abs product" style="left:599px">
    <svg class="product-shot" viewBox="0 0 170 217" role="img" aria-label="Square black patch with multicolour printed mascot artwork">
      <defs><linearGradient id="patch" x1="0" y1="0" x2="1" y2="1"><stop offset="0" stop-color="#2a2a2a"/><stop offset="0.5" stop-color="#3a2d4a"/><stop offset="1" stop-color="#1c1c1c"/></linearGradient></defs>
      <rect x="2" y="32" width="166" height="168" rx="18" fill="#111"/>
      <rect x="12" y="42" width="146" height="148" rx="12" fill="url(#patch)"/>
    </svg>
    <p class="product-label">PATCHES &amp;<br>TRANSFERS</p>
  </section>

  <svg class="abs warning-icon" viewBox="0 0 48 42" aria-hidden="true">
    <path d="M24 2 L46 40 L2 40 Z" fill="var(--orange)" stroke="var(--orange)" stroke-width="3" stroke-linejoin="round"/>
    <rect x="22" y="14" width="4" height="14" rx="2" fill="#fff"/>
    <circle cx="24" cy="33" r="2.4" fill="#fff"/>
  </svg>
  <p class="abs warning-text"><b>WARNING:</b> These shirts may cause increased shop morale, envy<br>from competitors and a high volume of customer demand.</p>

  <section class="abs services">
    <svg class="abs service-icon" style="left:54px" viewBox="0 0 58 58" fill="none" stroke="#fff" stroke-width="2.2" stroke-linejoin="round" aria-hidden="true">
      <path d="M4 18 L32 6 L54 16 L26 28 Z"/><path d="M4 18 L4 42 L26 54 L26 28"/><path d="M54 16 L54 40 L26 54"/><path d="M16 13 L42 23 L42 33"/><rect x="10" y="38" width="8" height="7"/>
    </svg>
    <div class="abs service-copy" style="left:127px"><h3>NO INVENTORY</h3>We produce what<br>you need, when<br>you need it.</div>
    <div class="abs divider" style="left:270px"></div>
    <svg class="abs service-icon" style="left:295px" viewBox="0 0 58 58" fill="none" stroke="#fff" stroke-width="2.2" stroke-linejoin="round" aria-hidden="true">
      <rect x="6" y="10" width="46" height="31" rx="2"/><path d="M1 46 L57 46"/><path d="M24 46 L24 50 L34 50 L34 46"/>
    </svg>
    <div class="abs service-copy" style="left:379px"><h3>ONLINE STORES</h3>Branded merch<br>stores for teams,<br>schools, and shops.</div>
    <div class="abs divider" style="left:530px"></div>
    <svg class="abs service-icon" style="left:558px" viewBox="0 0 58 58" fill="none" stroke="#fff" stroke-width="2.2" stroke-linejoin="round" aria-hidden="true">
      <rect x="2" y="12" width="36" height="28"/><path d="M38 20 L48 20 L56 30 L56 40 L38 40"/><circle cx="13" cy="42" r="5" fill="var(--navy)"/><circle cx="47" cy="42" r="5" fill="var(--navy)"/>
    </svg>
    <div class="abs service-copy" style="left:642px"><h3>DIRECT SHIPPING</h3>We pack and ship<br>orders straight to<br>your destination.</div>
  </section>

  <div class="abs footer-square"></div>
  <div class="abs footer-name">COPPER HOLLOW GRAPHICS</div>
  <div class="abs about">
    <h3>ABOUT US:</h3>
    <p>Copper Hollow Graphics is a second-generation screen printing company in Ashby Falls, VA. For over 45 years, we've specialized in high-quality custom apparel and merchandise.</p>
  </div>
  <div class="abs contact">
    <h3>CONTACT COPPER HOLLOW GRAPHICS:</h3>
    <p class="phone">555-014-2283</p>
    <p class="web">copperhollowtees.com &nbsp;//&nbsp; info@copperhollowtees.com</p>
  </div>
</main>
</body>
</html>
```